Business card for wedding & event planning company

I'm looking for a well designed double sided business card to represent my wedding and event planning company.

It should include the fact we manage the following events:
Weddings, birthdays, conferences, product launches, fashion shows & conventions
in the following areas:
Wiltshire, Oxfordshire, Berkshire & London

My contact details to be included are:

Moira Stanwick
07514 283640
moira@bluefernevents.co.uk
www.bluefernevents.co.uk

My logo can be found at the following Filebarn location:
AI file: https://www.filebarn.example/s/k3mxpw8rt51bn7d/logo_sourcefile.ai
PNG file:
https://www.filebarn.example/s/h6qvlz2ncy90tue/logo_image.png

Target Market(s)

women aged 30-55

Industry/Entity Type

Wedding

Contact Information for Business Card

in the following areas:

Moira Stanwick
Event Planner
07514 283640

Font styles to use
Serif
Sans Serif
Script

Requirements
Must have
• Purple and white colour scheme
Should not have
• Black background
• Please don't submit any of the see-through business card designs.

```html
<!DOCTYPE html>
<html lang="en">
<head>
<meta charset="utf-8">
<title>Blue Fern Events – Business Card</title>
<link rel="stylesheet" href="https://fonts.googleapis.com/css2?family=Source+Sans+3:wght@400;600;700&display=swap">
<style>
  :root {
    --backdrop: #1d1d1f;
    --card: #303033;
    --card-edge: #3a3a3e;
    --purple: #9a2fa6;
    --purple-soft: #7e2a8a;
    --white: #f4f4f6;
    --divider: #45454a;
  }
  * { margin: 0; padding: 0; box-sizing: border-box; }
  html, body {
    width: 1200px;
    height: 900px;
    overflow: hidden;
    background: var(--backdrop);
    font-family: "Source Sans 3", "Myriad Pro", Arial, sans-serif;
    color: var(--white);
  }
  .canvas { position: relative; width: 1200px; height: 900px; }
  .card {
    position: absolute;
    left: 331px;
    width: 542px;
    height: 316px;
    border-radius: 18px;
    background: var(--card);
    border: 1px solid var(--card-edge);
  }
  .card--front { top: 118px; }
  .card--back { top: 488px; }

  /* Front */
  .brand {
    position: absolute;
    left: 30px;
    top: 92px;
    width: 200px;
    text-align: center;
  }
  .brand__mark {
    display: block;
    margin: 0 auto 14px;
  }
  .brand__name {
    font-size: 23px;
    font-weight: 400;
    color: var(--purple);
    letter-spacing: 0.5px;
    white-space: nowrap;
  }
  .divider {
    position: absolute;
    left: 236px;
    top: 78px;
    width: 1px;
    height: 160px;
    background: var(--divider);
  }
  .contact {
    position: absolute;
    left: 246px;
    top: 102px;
  }
  .contact__name {
    font-size: 24px;
    font-weight: 600;
    color: var(--purple);
    margin-bottom: 26px;
  }
  .contact__list { list-style: none; font-size: 16.5px; line-height: 21.5px; }
  .contact__label { color: var(--purple); display: inline-block; width: 20px; font-size: 14px; }

  /* Back */
  .column-head { font-size: 16.5px; font-weight: 700; }
  .areas {
    position: absolute;
    right: 339px;
    top: 88px;
    text-align: right;
  }
  .areas .column-head { margin-right: -26px; margin-bottom: 10px; }
  .events {
    position: absolute;
    left: 357px;
    top: 88px;
  }
  .events .column-head { margin-left: 9px; margin-bottom: 10px; }
  .list { list-style: none; font-size: 16.5px; line-height: 23.5px; }
  .back-mark {
    position: absolute;
    left: 200px;
    top: 100px;
  }
</style>
</head>
<body>
<main class="canvas">
  <section class="card card--front" aria-label="Business card front">
    <div class="brand">
      <svg class="brand__mark" width="44" height="44" viewBox="0 0 44 44" aria-hidden="true">
        <circle cx="22" cy="22" r="19" fill="none" stroke="var(--purple)" stroke-width="2"/>
      </svg>
      <div class="brand__name">Blue Fern Events</div>
    </div>
    <div class="divider"></div>
    <div class="contact">
      <h1 class="contact__name">Moira Stanwick</h1>
      <ul class="contact__list">
        <li><span class="contact__label">T:</span>07514 283640</li>
        <li><span class="contact__label">E:</span>moira@bluefernevents.co.uk</li>
        <li><span class="contact__label">W:</span>www.bluefernevents.co.uk</li>
      </ul>
    </div>
  </section>

  <section class="card card--back" aria-label="Business card back">
    <div class="areas">
      <h2 class="column-head">Convention Areas</h2>
      <ul class="list">
        <li>Wiltshire</li>
        <li>Oxfordshire</li>
        <li>Berkshire</li>
        <li>London</li>
      </ul>
    </div>
    <svg class="back-mark" width="120" height="120" viewBox="0 0 120 120" aria-hidden="true">
      <circle cx="60" cy="60" r="55" fill="none" stroke="var(--purple-soft)" stroke-width="2.5"/>
    </svg>
    <div class="events">
      <h2 class="column-head">Events</h2>
      <ul class="list">
        <li>Weddings</li>
        <li>Birthdays</li>
        <li>Conferences</li>
        <li>Product Launches</li>
        <li>Fashion Shows</li>
      </ul>
    </div>
  </section>
</main>
</body>
</html>
```